Tellmora Corporate Stationery

Look for design of all new corporate stationery for an existing insurance broking business that is going through a redesign and move from older partners to younger family members. New Logo is attached. Company is Brisbane based.
Colours in the Logo is Hex #43bed8 and website features a lot of hex #17b8d8. Website front page "A plan to protect you" - headline. "Professional and Individual advice to protect your greatest assets" - tagline.

Stationery required: Business Cards, Letter head, Thank-you cards, Birthday cards, Presentation folders, With Compliment slips and a powerpoint template. We also would like to send a card to all customers with the something along of the lines of "something new".

Target Market(s)

Customers of Insurance business looking at superannuation, life and income protection insurance, investment advice and wills

Industry/Entity Type

Insurance Broker

Font styles to use
Other font styles liked:
• same as logo

Requirements
Must have
• The above designs for new stationery for the new business including:
• Business Cards, Letter head, Thank-you cards, Birthday cards, Presentation folders, With Compliment slips and a powerpoint template. We also would like to send a card to all customers with the something along of the lines of "something new".
Nice to have
• It is a new look - long time family business being passed to next generation - big focus on advice for YOU, individual advice etc..

```html
<!DOCTYPE html>
<html lang="en">
<head>
<meta charset="utf-8">
<title>Tellmora Business Card</title>
<link rel="stylesheet" href="https://fonts.googleapis.com/css2?family=Open+Sans:wght@400;600&display=swap">
<style>
  :root {
    --backdrop: #262626;
    --brand-blue: #3dbfd9;
    --card-white: #ffffff;
    --ink-grey: #555a5e;
    --rule-grey: #6b6f72;
    --font-main: "Open Sans", Arial, sans-serif;
  }
  * { margin: 0; padding: 0; box-sizing: border-box; }
  html, body {
    width: 1200px; height: 987px; overflow: hidden;
    background: var(--backdrop);
    font-family: var(--font-main);
  }
  .canvas { position: relative; width: 1200px; height: 987px; }
  .card {
    position: absolute; left: 293px; width: 615px; height: 352px;
    box-shadow: 0 4px 14px rgba(0,0,0,0.45);
  }
  .card-front { top: 130px; background: var(--card-white); }
  .card-back { top: 505px; background: var(--brand-blue); }

  .logo-tab {
    position: absolute; left: 424px; top: 0; width: 80px; height: 44px;
    background: var(--brand-blue);
  }
  .logo-dot {
    position: absolute; left: 428px; top: 24px; width: 72px; height: 72px;
    border-radius: 50%; background: var(--brand-blue);
    border: 6px solid var(--card-white);
  }
  .brand-name {
    position: absolute; right: 35px; top: 106px; text-align: right;
    color: var(--brand-blue); font-weight: 600; line-height: 1;
  }
  .brand-name .word { display: block; font-size: 34px; letter-spacing: 1px; }
  .brand-name .sub { display: block; font-size: 16px; letter-spacing: 1px; margin-top: 4px; }

  .name-bar {
    position: absolute; left: 0; top: 219px; width: 11px; height: 44px;
    background: var(--brand-blue);
  }
  .person-name {
    position: absolute; left: 25px; top: 213px;
    font-size: 21px; font-weight: 600; color: var(--brand-blue); letter-spacing: .3px;
  }
  .person-role {
    position: absolute; left: 25px; top: 243px;
    font-size: 15px; color: var(--ink-grey);
  }
  .mobile {
    position: absolute; right: 30px; top: 242px;
    font-size: 15px; color: var(--ink-grey);
    display: flex; align-items: center; gap: 8px;
  }
  .divider {
    position: absolute; left: 25px; top: 270px; width: 555px; height: 1px;
    background: var(--rule-grey);
  }
  .contact-col {
    position: absolute; top: 278px;
    font-size: 15.5px; line-height: 27px; color: var(--ink-grey);
  }
  .address { left: 25px; }
  .phones { left: 252px; }
  .web { left: 413px; }
  .phones .row { display: flex; align-items: center; gap: 7px; }
  .icon { width: 15px; height: 15px; fill: var(--brand-blue); }

  .back-brand {
    position: absolute; left: 18px; top: 148px;
    color: var(--card-white); font-weight: 600; line-height: 1;
  }
  .back-brand .word { display: block; font-size: 33px; letter-spacing: 1px; }
  .back-brand .sub { display: block; font-size: 16px; letter-spacing: 1px; margin: 4px 0 0 22px; }
  .back-web {
    position: absolute; left: 18px; top: 316px;
    color: var(--card-white); font-size: 14px; letter-spacing: 4px;
  }
</style>
</head>
<body>
<main class="canvas">
  <section class="card card-front">
    <div class="logo-tab"></div>
    <div class="logo-dot"></div>
    <div class="brand-name">
      <span class="word">TELLMORA</span>
      <span class="sub">FINANCIAL GROUP</span>
    </div>

    <div class="name-bar"></div>
    <div class="person-name">MARCUS HALE</div>
    <div class="person-role">CEO/FOUNDER</div>
    <div class="mobile">
      <span>0412 557 839</span>
      <svg class="icon" viewBox="0 0 16 16" aria-hidden="true">
        <path d="M4 0h8a1.5 1.5 0 0 1 1.5 1.5v13A1.5 1.5 0 0 1 12 16H4a1.5 1.5 0 0 1-1.5-1.5v-13A1.5 1.5 0 0 1 4 0zm.5 2v10.5h7V2zm3.5 11.3a.9.9 0 1 0 0 1.8.9.9 0 0 0 0-1.8z"/>
      </svg>
    </div>
    <div class="divider"></div>

    <div class="contact-col address">
      <div>214 Wattle Grove Road</div>
      <div>Brisbane, Queensland 4000</div>
    </div>
    <div class="contact-col phones">
      <div class="row">
        <svg class="icon" viewBox="0 0 16 16" aria-hidden="true">
          <path d="M3.6 1l2.3 2.6-1.3 2.1a9 9 0 0 0 5.7 5.7l2.1-1.3L15 12.4 13.3 15C6.6 14.6 1.4 9.4 1 2.7z"/>
        </svg>
        <span>07 3184 2260</span>
      </div>
      <div class="row">
        <svg class="icon" viewBox="0 0 16 16" aria-hidden="true">
          <path d="M4 1h8v4H4zM1 6h14v6h-2v3H3v-3H1zm4 4v3.5h6V10z"/>
        </svg>
        <span>07 3184 2261</span>
      </div>
    </div>
    <div class="contact-col web">
      <div>hello@tellmora.au</div>
      <div>www.tellmora.au</div>
    </div>
  </section>

  <section class="card card-back">
    <div class="back-brand">
      <span class="word">TELLMORA</span>
      <span class="sub">FINANCIAL GROUP</span>
    </div>
    <div class="back-web">www.tellmora.au</div>
  </section>
</main>
</body>
</html>
```